Brookvale Estates LLC stationary for a real estate property management company.

Create stationary (letterhead, envelopes, business cards) using Brookvale Estates LLC logo as primary creative element. Stationary design needs to be horizontal, leaving as much space as possible for correspondence copy. See attached Creative Brief and past stationary files for details.

Target Market(s)

Prospective apartment residents and current residents, vendors, and government agencies.

Industry/Entity Type

Property Management

Contact Information for Business Card

Business card employee title: Property Manager. Should include address, phone, fax, email, website, slogan, and Brookvale Estates logo.

Font styles to use
Sans Serif

Colors
0592cd
000000

Requirements
Must have
• Tone should be conservative, institutional, business (i.e. banking, finance, real estate). Must include: address, phone, fax, website, and slogan (see attached Creative Brief). Should be a horizontal design, leaving as much room as possible for letter correspondence copy.
Nice to have
• Please use an Arial or Helvetica style font.
Should not have
• Letterhead layout should leave as much room as possible for copy.

```html
<!DOCTYPE html>
<html lang="en">
<head>
<meta charset="utf-8">
<title>Brookvale Estates LLC – Stationery</title>
<link href="https://fonts.googleapis.com/css2?family=Arimo:wght@400;700&family=Source+Sans+3:wght@400&display=swap" rel="stylesheet">
<style>
  :root {
    --brand-blue: #0a67a6;
    --charcoal: #3d3f42;
    --ink: #333333;
    --muted: #555555;
    --paper: #f7f7f7;
    --backdrop: #e4e2df;
    --white: #ffffff;
  }
  * { box-sizing: border-box; margin: 0; padding: 0; }
  html, body { width: 1200px; height: 754px; overflow: hidden; }
  body { background: var(--backdrop); font-family: "Arimo", Arial, sans-serif; color: var(--ink); position: relative; }

  .sheet { position: absolute; background: var(--paper); box-shadow: 0 2px 6px rgba(0,0,0,.18); overflow: hidden; }

  .brand-lockup { display: flex; align-items: center; gap: 7px; }
  .brand-lockup .brand-mark { background: var(--brand-blue); flex: none; }
  .brand-lockup .brand-name { color: var(--brand-blue); font-weight: 700; line-height: 1.05; text-transform: uppercase; }

  /* Letterhead */
  .letterhead { left: 36px; top: 32px; width: 488px; height: 688px; }
  .letterhead .brand-lockup { position: absolute; left: 48px; top: 58px; }
  .letterhead .brand-mark { width: 24px; height: 24px; }
  .letterhead .brand-name { font-size: 17px; }
  .letterhead .contact-block { position: absolute; left: 316px; top: 52px; border-left: 1px solid #cfcfcf; padding-left: 10px; font-size: 7.6px; line-height: 10px; color: var(--ink); height: 54px; }
  .contact-block .contact-row { display: flex; align-items: center; gap: 4px; }
  .contact-block svg { width: 8px; height: 8px; fill: var(--brand-blue); }
  .letter-body { position: absolute; left: 49px; top: 193px; width: 395px; font-family: "Source Sans 3", Arial, sans-serif; }
  .letter-body .salutation { font-size: 13.5px; color: var(--muted); margin-bottom: 22px; }
  .letter-body p { font-size: 7.4px; line-height: 11.8px; color: var(--muted); margin-bottom: 11.8px; text-align: justify; }
  .letter-body .closing { margin-top: 22px; margin-bottom: 8px; }
  .signature-area { width: 62px; height: 26px; background: linear-gradient(90deg, rgba(40,40,40,.08), rgba(40,40,40,.02)); }

  .footer-band { position: absolute; left: 0; right: 0; bottom: 0; height: 16px; background: var(--brand-blue); color: var(--white); font-size: 7.5px; letter-spacing: 1.4px; text-align: center; line-height: 16px; }

  /* Business card front */
  .card-front { left: 578px; top: 74px; width: 266px; height: 152px; background: #efefef; }
  .card-front .edge-band { position: absolute; left: 0; top: 0; width: 54px; height: 100%; background: var(--brand-blue); }
  .card-front .feature-panel { position: absolute; left: 54px; top: 0; width: 62px; height: 100%; background: #e6e6e6; }
  .card-front .card-details { position: absolute; right: 12px; top: 16px; text-align: right; }
  .card-front .brand-lockup { justify-content: flex-end; }
  .card-front .brand-mark { width: 16px; height: 16px; }
  .card-front .brand-name { font-size: 13px; text-align: right; }
  .card-front .person-name { color: var(--brand-blue); font-weight: 700; font-size: 9px; margin-top: 8px; }
  .card-front .person-title { font-size: 6.8px; color: var(--ink); }
  .card-front .address { font-size: 5.8px; line-height: 7.5px; margin-top: 7px; }
  .card-front .contacts { font-size: 5.8px; line-height: 7.5px; margin-top: 6px; }
  .card-front .slogan { font-size: 6px; font-weight: 700; color: var(--brand-blue); margin-top: 4px; }

  /* Business card back */
  .card-back { left: 876px; top: 144px; width: 268px; height: 150px; background: var(--charcoal); display: flex; align-items: center; justify-content: center; }
  .card-back .brand-mark { width: 26px; height: 26px; }
  .card-back .brand-name { font-size: 17px; }

  /* Envelope back */
  .envelope-back { left: 616px; top: 350px; width: 546px; height: 248px; background: #eeeeee; }
  .envelope-back .flap { position: absolute; left: 0; top: 0; width: 100%; height: 92px; }
  .envelope-back .brand-lockup { position: absolute; left: 218px; top: 30px; }
  .envelope-back .brand-mark { width: 18px; height: 18px; }
  .envelope-back .brand-name { font-size: 12px; }

  /* Envelope front */
  .envelope-front { left: 546px; top: 470px; width: 550px; height: 250px; }
  .envelope-front .return-address { position: absolute; left: 24px; top: 24px; }
  .envelope-front .brand-mark { width: 22px; height: 22px; }
  .envelope-front .brand-name { font-size: 14px; }
  .envelope-front .address { font-size: 7.6px; line-height: 9.6px; margin-top: 4px; padding-left: 15px; }
</style>
</head>
<body>

<section class="sheet letterhead" aria-label="Letterhead">
  <div class="brand-lockup">
    <span class="brand-mark"></span>
    <span class="brand-name">Brookvale<br>Estates LLC</span>
  </div>
  <div class="contact-block">
    <div>2750 Alder Creek Road #B210</div>
    <div>Fresno, CA 93711</div>
    <div class="contact-row"><svg viewBox="0 0 24 24"><path d="M6.6 10.8a15 15 0 006.6 6.6l2.2-2.2a1 1 0 011-.25 11.4 11.4 0 003.6.6 1 1 0 011 1V20a1 1 0 01-1 1A17 17 0 013 4a1 1 0 011-1h3.5a1 1 0 011 1c0 1.25.2 2.45.6 3.6a1 1 0 01-.25 1z"/></svg>559-410-2276</div>
    <div class="contact-row"><svg viewBox="0 0 24 24"><path d="M6 3h12v5H6zM3 9h18v9h-3v3H6v-3H3zm5 6v4h8v-4z"/></svg>559-410-2291</div>
    <div class="contact-row"><svg viewBox="0 0 24 24"><path d="M2 5h20v14H2zm2 2v.5l8 5 8-5V7z"/></svg>daniel@brookvaleestates.us</div>
  </div>

  <div class="letter-body">
    <div class="salutation">Dear Mr. Collins,</div>
    <p>Lorem ipsum dolor sit amet, consectetur adipiscing elit. Donec orci purus, luctus vitae dignissim eu, iaculis sed purus. Vivamus faucibus, ipsum nec aliquet viverra, leo mauris condimentum ligula, sit amet sagittis enim ligula quis arcu. Nam egestas tortor id nisi porttitor mattis. In tortor ante, ultricies in suscipit a, tempus non massa. Vivamus et auctor mi. Fusce vel massa nulla. Phasellus nec eros mauris, et scelerisque orci.</p>
    <p>Donec malesuada orci vitae nulla accumsan porta a id massa. Quisque accumsan iaculis magna sit amet fringilla. Maecenas consequat, magna eget tincidunt semper, odio nibh rutrum mi, id feugiat ante nisi eu risus. Vestibulum nunc orci, rhoncus a placerat in, ultricies in mi. Cras mattis varius eros, vel fringilla nisi suscipit eget. Quisque scelerisque sagittis nulla at porttitor.</p>
    <p>Sed id augue vitae urna euismod commodo aliquet a quam. Pellentesque arcu velit, cursus et malesuada ut, consequat et diam. Nullam erat sem, rhoncus id ullamcorper vitae, rhoncus et arcu. In ultricies ultricies nulla, ut rutrum nisi iaculis at. Donec eu magna a metus ornare faucibus. Fusce aliquet faucibus ultricies. Morbi semper, est id tincidunt gravida, sem arcu adipiscing lacus, ac bibendum nulla leo eu purus. Quisque nec diam sed risus consectetur a accumsan quis quis nibh. Vestibulum id purus lorem.</p>
    <p>It is a long established fact that a reader will be distracted by the readable content of a page when looking at its layout. The point of using Lorem Ipsum is that it has a more-or-less normal distribution of letters, as opposed to using 'Content here, content here', making it look like readable English. Many desktop publishing packages</p>
    <p class="closing">Sincerely,</p>
    <div class="signature-area" role="img" aria-label="Handwritten signature"></div>
  </div>

  <div class="footer-band">www.brookvaleestates.us</div>
</section>

<section class="sheet card-front" aria-label="Business card front">
  <div class="edge-band"></div>
  <div class="feature-panel"></div>
  <div class="card-details">
    <div class="brand-lockup">
      <span class="brand-mark"></span>
      <span class="brand-name">Brookvale<br>Estates LLC</span>
    </div>
    <div class="person-name">DANIEL HARTLEY</div>
    <div class="person-title">Property Manager</div>
    <div class="address">2750 Alder Creek Road #B210<br>Fresno, CA 93711</div>
    <div class="contacts">Phone: 559-410-2276<br>Fax: 559-410-2291<br>daniel@brookvaleestates.us<br>www.brookvaleestates.us</div>
    <div class="slogan">Multifamily Property Management</div>
  </div>
</section>

<section class="sheet card-back" aria-label="Business card back">
  <div class="brand-lockup">
    <span class="brand-mark"></span>
    <span class="brand-name">Brookvale<br>Estates LLC</span>
  </div>
</section>

<section class="sheet envelope-back" aria-label="Envelope back">
  <svg class="flap" viewBox="0 0 546 92" preserveAspectRatio="none">
    <path d="M0 0H546V6C540 40 530 78 500 88Q494 92 480 92H66Q52 92 46 88C18 78 8 40 0 6Z" fill="#3d3f42"/>
  </svg>
  <div class="brand-lockup">
    <span class="brand-mark"></span>
    <span class="brand-name">Brookvale<br>Estates LLC</span>
  </div>
</section>

<section class="sheet envelope-front" aria-label="Envelope front">
  <div class="return-address">
    <div class="brand-lockup">
      <span class="brand-mark"></span>
      <span class="brand-name">Brookvale<br>Estates LLC</span>
    </div>
    <div class="address">2750 Alder Creek Road #B210<br>Fresno, CA 93711</div>
  </div>
  <div class="footer-band">www.brookvaleestates.us</div>
</section>

</body>
</html>
```